Zielgruppe
Produtkion von Bioeiern. Wir suchen ein Design für eine Eierpappe. Im Focus stehen die Aspekte Regionalität und Bio
Zielgruppe: Endverbraucher
Aufgabenstellung
Nicht zu bunt eher natur und bodenständig.
Es müssen diverse Sigel (Eu -Bio, Verbandlogo und VRN-Sigel) und EAN auf die Pappe.
Es handelt sich um 6er Pappen und 10er Pappen
Vielleicht gibt es auch Vorschläge zu neuen Verpackungen, also nicht die standrad-Eierpappe....
Nicht unbedingt ein Foto mit dem Huhn auf der grünen Wiese. eher in die Richtung Kartoon oder Karikatur.

```html
<!DOCTYPE html>
<html lang="de">
<head>
<meta charset="utf-8">
<title>Bio Eier – Etikett</title>
<link href="https://fonts.googleapis.com/css2?family=Dancing+Script:wght@600;700&family=Open+Sans:wght@400;600&family=Lora:ital@0;1&display=swap" rel="stylesheet">
<style>
  :root{
    --bg:#f3f3f0;
    --band:#1d5830;
    --band-dark:#164826;
    --beige:#c8b9a0;
    --beige-light:#d9ccb6;
    --ink:#54442f;
    --white:#ffffff;
    --seal-green:#6aa43a;
    --seal-red:#c8322b;
  }
  *{margin:0;padding:0;box-sizing:border-box}
  html,body{width:1200px;height:829px;overflow:hidden;background:var(--bg)}
  .canvas{position:relative;width:1200px;height:829px}
  .label{
    position:absolute;left:430px;top:40px;width:340px;height:749px;
    background:var(--band);overflow:hidden;
  }
  .label__mascot{
    position:absolute;left:38px;top:-20px;width:264px;height:250px;
    border-radius:50%;background:var(--white);
  }
  .label__badge-main{
    position:absolute;left:43px;top:158px;width:254px;height:132px;
    border-radius:50%;background:var(--beige);border:3px solid var(--band);
    text-align:center;
  }
  .label__bio{
    display:block;font-family:"Dancing Script",cursive;font-weight:700;
    font-size:76px;line-height:1;color:var(--band);margin-top:6px;
  }
  .label__eier{
    display:block;font-family:"Open Sans",sans-serif;font-weight:400;
    font-size:40px;line-height:1;color:var(--band);margin-top:-8px;
  }
  .label__claim{
    position:absolute;left:0;right:0;top:300px;text-align:center;
    font-family:"Dancing Script",cursive;font-weight:600;font-size:38px;
    line-height:1.02;color:var(--white);transform:rotate(-4deg);
  }
  .label__count{
    position:absolute;left:0;right:0;top:402px;text-align:center;
    font-family:"Lora",serif;font-style:italic;font-size:27px;color:var(--white);
  }
  .label__strip{
    position:absolute;left:110px;top:450px;width:120px;height:299px;
    background:var(--beige);
  }
  .label__window{
    position:absolute;left:80px;top:458px;width:180px;height:150px;
    border-radius:50%;background:var(--band-dark);
    box-shadow:inset 0 6px 14px rgba(0,0,0,.35);
  }
  .label__address{
    position:absolute;left:110px;top:650px;width:120px;text-align:center;
    font-family:"Open Sans",sans-serif;font-size:15px;line-height:1.4;color:var(--ink);
  }
  .seal{position:absolute;top:655px}
  .seal--eu{left:18px;width:80px;height:54px;background:var(--seal-green)}
  .seal--farm{left:248px;top:642px;width:76px;height:76px;border-radius:50%;
    background:var(--white);border:5px solid var(--seal-red)}
</style>
</head>
<body>
<main class="canvas">
  <section class="label">
    <div class="label__mascot" role="img" aria-label="Cartoon-Huhn mit erhobenem Daumen"></div>
    <div class="label__badge-main">
      <span class="label__bio">Bio</span>
      <span class="label__eier">Eier</span>
    </div>
    <p class="label__claim">frisch aus<br>der Region!</p>
    <p class="label__count">6 Stück</p>
    <div class="label__strip"></div>
    <div class="label__window"></div>
    <p class="label__address">Adr. Betrieb<br>PLZ<br>Ortschaft</p>
    <div class="seal seal--eu" role="img" aria-label="Bio-Siegel"></div>
    <div class="seal seal--farm" role="img" aria-label="Herkunftssiegel"></div>
  </section>
</main>
</body>
</html>
```